Facebook post - Kestrel Bay Finishes has arrived to make your tiles smile!

Kestrel Bay Finishes would like to release a Facebook post calling out to the market that we have arrived. The company has a new and fresh branding aiming for a female demographic between the ages of 40 and 55 located in the South West of Western Australia. The company image MUST be centered around trust! Our Primary aim is to create an uncompromising trust from the very first impression. Our logo tag line is, 'We love to make your tiles smile'.
I need 5 x facebook template designs and also 5 x posts.
Our 1st campaign is to be 5 x posts centered around the arrival of this fantastic new company.
We are company that provides the services of:
- Grout and silicone repair.
- Broken or drummy tile replacement and;
- Grout sealing
Dont forget that we must communicate TRUST and the we love to make your tiles SMILE!

```html
<!DOCTYPE html>
<html lang="en">
<head>
<meta charset="utf-8">
<title>Kestrel Bay Finishes – We love to make your tiles smile</title>
<link rel="stylesheet" href="https://fonts.googleapis.com/css2?family=Oswald:wght@300;400&display=swap">
<style>
  :root {
    --tile-white: #ffffff;
    --tile-shade: #f3f4f5;
    --grout: #d9dadc;
    --grout-shadow: #c4c6c9;
    --brand-blue: #2fa8dc;
    --ink-grey: #4a4b4d;
  }
  html, body {
    margin: 0;
    padding: 0;
    width: 1200px;
    height: 444px;
    overflow: hidden;
    background: var(--tile-white);
  }
  .post {
    display: block;
    width: 1200px;
    height: 444px;
  }
  .tile-face { fill: url(#tileGloss); }
  .grout-line {
    stroke: var(--grout);
    stroke-width: 5;
    fill: none;
  }
  .grout-shadow {
    stroke: var(--grout-shadow);
    stroke-width: 1.5;
    fill: none;
    opacity: 0.6;
  }
  .tagline {
    font-family: "Oswald", sans-serif;
    font-weight: 300;
    letter-spacing: 4px;
  }
  .tagline--blue { fill: var(--brand-blue); }
  .tagline--grey { fill: var(--ink-grey); }
  .brand-name {
    font-family: "Oswald", sans-serif;
    font-weight: 300;
    fill: var(--brand-blue);
    letter-spacing: 2px;
  }
</style>
</head>
<body>
<svg class="post" viewBox="0 0 1200 444" width="1200" height="444" xmlns="http://www.w3.org/2000/svg">
  <defs>
    <linearGradient id="tileGloss" x1="0" y1="0" x2="1" y2="1">
      <stop offset="0" stop-color="var(--tile-white)"/>
      <stop offset="1" stop-color="var(--tile-shade)"/>
    </linearGradient>
  </defs>

  <rect class="tile-face" x="0" y="0" width="1200" height="444"/>

  <g class="tiled-wall" transform="skewY(-10)">
    <g class="grout-grid">
      <line class="grout-line" x1="240" y1="-400" x2="240" y2="900"/>
      <line class="grout-line" x1="600" y1="-400" x2="600" y2="900"/>
      <line class="grout-line" x1="960" y1="-400" x2="960" y2="900"/>
      <line class="grout-line" x1="-50" y1="-141" x2="1300" y2="-141"/>
      <line class="grout-line" x1="-50" y1="219" x2="1300" y2="219"/>
      <line class="grout-line" x1="-50" y1="579" x2="1300" y2="579"/>
      <line class="grout-shadow" x1="242.5" y1="-400" x2="242.5" y2="900"/>
      <line class="grout-shadow" x1="602.5" y1="-400" x2="602.5" y2="900"/>
      <line class="grout-shadow" x1="962.5" y1="-400" x2="962.5" y2="900"/>
      <line class="grout-shadow" x1="-50" y1="221.5" x2="1300" y2="221.5"/>
      <line class="grout-shadow" x1="-50" y1="581.5" x2="1300" y2="581.5"/>
    </g>

    <text class="brand-name" x="420" y="330" font-size="40" text-anchor="middle">Kestrel Bay Finishes</text>

    <g class="tagline-block">
      <text class="tagline tagline--blue" x="663" y="279" font-size="64" textLength="226" lengthAdjust="spacingAndGlyphs">WE LOVE</text>
      <text class="tagline tagline--grey" x="663" y="343" font-size="64" textLength="233" lengthAdjust="spacingAndGlyphs">TO MAKE</text>
      <text class="tagline tagline--grey" x="663" y="396" font-size="48" textLength="233" lengthAdjust="spacingAndGlyphs">YOUR TILES</text>
      <text class="tagline tagline--blue" x="663" y="503" font-size="88" textLength="240" lengthAdjust="spacingAndGlyphs">SMILE!</text>
    </g>
  </g>
</svg>
</body>
</html>
```